I need a new business card designed, we recently rebranded and I need to get a fresh design to match our new logo, colours and branding.

Details:

Derek Havill | Founder & CEO
Address: 7 Marlowfern Lane, #09-14 Tavenport Crest, Singapore 318547
Tel: +65 93568214
Web: www.frostkarta.com.sg
hello@frostkarta.com.sg

I've attached my old card as well

Industry/Entity Type

Business

Requirements
Must have
• Front and Back
Interesting use of logo
Correct use of colour scheme

```html
<!DOCTYPE html>
<html lang="en">
<head>
<meta charset="utf-8">
<title>frostkarta business card</title>
<link rel="stylesheet" href="https://fonts.googleapis.com/css2?family=PT+Sans:wght@400;700&display=swap">
<style>
  :root {
    --stage: #dcd8d2;
    --card: #e8e7e2;
    --card-edge: #b9b6b0;
    --ice-blue: #1aaeea;
    --ice-faint: #cfe2e7;
    --cocoa: #6b605a;
    --rule: #7d7873;
    --white: #ffffff;
  }
  * { box-sizing: border-box; margin: 0; padding: 0; }
  html, body { width: 1200px; height: 1000px; overflow: hidden; }
  body {
    position: relative;
    background: var(--stage);
    font-family: "PT Sans", sans-serif;
    color: var(--cocoa);
  }
  .card {
    position: absolute;
    background: var(--card);
    border: 1px solid var(--card-edge);
    overflow: hidden;
  }

  /* back of card */
  .card-back { left: 318px; top: 88px; width: 730px; height: 416px; }
  .card-back .brand-mark {
    position: absolute; left: 220px; top: 160px;
    width: 84px; height: 84px; border-radius: 50%;
    background: var(--ice-blue);
  }
  .card-back .brand-name {
    position: absolute; left: 311px; top: 156px;
    font-size: 50px; font-weight: 700; line-height: 1; color: var(--cocoa);
  }
  .card-back .brand-tagline {
    position: absolute; left: 313px; top: 220px;
    font-size: 12px; font-weight: 700; letter-spacing: 0.6px; color: var(--ice-blue);
  }

  /* front of card */
  .card-front { left: 50px; top: 457px; width: 730px; height: 418px; }
  .card-front .watermark {
    position: absolute; left: 185px; top: 138px;
    width: 290px; height: 290px; border-radius: 50%;
    background: var(--ice-faint);
  }
  .card-front .header-rule {
    position: absolute; left: 0; top: 117px; width: 714px; height: 1px; background: var(--rule);
  }
  .card-front .brand-mark {
    position: absolute; left: 48px; top: 42px;
    width: 42px; height: 42px; border-radius: 50%; background: var(--ice-blue);
  }
  .card-front .brand-name {
    position: absolute; left: 96px; top: 42px;
    font-size: 28px; font-weight: 700; line-height: 1; color: var(--cocoa);
  }
  .card-front .brand-tagline {
    position: absolute; left: 97px; top: 74px;
    font-size: 7px; font-weight: 700; letter-spacing: 0.2px; color: var(--ice-blue);
  }
  .cursor { position: absolute; left: 200px; top: 85px; width: 12px; height: 19px; }
  .person-name {
    position: absolute; left: 457px; top: 30px;
    font-size: 35px; font-weight: 700; letter-spacing: 1.5px; line-height: 1; color: var(--ice-blue);
    white-space: nowrap;
  }
  .person-role {
    position: absolute; left: 458px; top: 66px;
    font-size: 23px; line-height: 1; color: var(--cocoa);
  }
  .scroll-track {
    position: absolute; right: 14px; top: 0; width: 1px; height: 100%; background: var(--card-edge);
  }
  .scroll-thumb {
    position: absolute; right: 4px; top: 40px; width: 9px; height: 59px;
    border-radius: 4px; background: var(--ice-blue);
  }

  .detail { position: absolute; }
  .detail-label {
    font-size: 12.5px; text-transform: uppercase; color: var(--cocoa); line-height: 1;
    margin-bottom: 18px;
  }
  .detail-value {
    position: relative;
    background: var(--ice-blue); color: var(--white);
    font-size: 16px; line-height: 20px; padding: 8px 8px;
  }
  .detail-value::before {
    content: ""; position: absolute; left: 18px; top: -15px;
    border-left: 9px solid transparent; border-right: 9px solid transparent;
    border-bottom: 16px solid var(--ice-blue);
  }
  .detail-email   { left: 47px;  top: 167px; width: 180px; }
  .detail-web     { left: 47px;  top: 265px; width: 180px; }
  .detail-contact { left: 460px; top: 167px; width: 166px; }
  .detail-address { left: 460px; top: 265px; width: 166px; }
  .detail-contact .detail-value { padding-left: 13px; }
  .detail-address .detail-value { padding: 7px 11px 8px; }
</style>
</head>
<body>

  <section class="card card-back" aria-label="Card back">
    <div class="brand-mark"></div>
    <div class="brand-name">frostkarta</div>
    <div class="brand-tagline">WEB DESIGN &amp; CONSULTANCY</div>
  </section>

  <section class="card card-front" aria-label="Card front">
    <div class="watermark"></div>
    <div class="brand-mark"></div>
    <div class="brand-name">frostkarta</div>
    <div class="brand-tagline">WEB DESIGN &amp; CONSULTANCY</div>
    <svg class="cursor" viewBox="0 0 12 19" aria-hidden="true">
      <path d="M1 1 L1 15 L4.5 11.5 L7 17.5 L9 16.6 L6.6 10.8 L11 10.8 Z" fill="#222" stroke="#fff" stroke-width="1"/>
    </svg>

    <div class="person-name">Derek Havill</div>
    <div class="person-role">Founder</div>

    <div class="header-rule"></div>
    <div class="scroll-track"></div>
    <div class="scroll-thumb"></div>

    <div class="detail detail-email">
      <div class="detail-label">Email</div>
      <div class="detail-value">www.frostkarta.com.sg</div>
    </div>
    <div class="detail detail-web">
      <div class="detail-label">Web site</div>
      <div class="detail-value">hello@frostkarta.com.sg</div>
    </div>
    <div class="detail detail-contact">
      <div class="detail-label">Contact</div>
      <div class="detail-value">+65&nbsp; 9356 8214</div>
    </div>
    <div class="detail detail-address">
      <div class="detail-label">Address</div>
      <div class="detail-value">7 Marlowfern Lane,<br>#09-14 Tavenport Crest,<br>Singapore 318547</div>
    </div>
  </section>

</body>
</html>
```